Breakfast Cafe - The Sunny Nook

It is for my breakfast and lunch cafe with a hawaiian / beach theme. I am open 7 days a week from 7am to 2pm. We serve traditional American food such as omelettes, pancakes, burgers and sandwiches. I'll upload my old card and my new logo to be used. We have a lot of day to day regulars who eat there during the week, our t-shirts actually say 'Locals Only' on them. Hope this helps. Thanks.

Target Market(s)

anyone who has an appetite!

Industry/Entity Type

American Restaurant

Contact Information for Business Card

4815C Marlow Grove Avenue
Long Beach, California
(555) 731-2294

Requirements
Must have
• Address and phone number easily readable.
Nice to have
• beach or tropical theme

```html
<!DOCTYPE html>
<html lang="en">
<head>
<meta charset="utf-8">
<title>The Sunny Nook – Business Card</title>
<link href="https://fonts.googleapis.com/css2?family=Oswald:wght@400;500&display=swap" rel="stylesheet">
<style>
  :root {
    --backdrop: #e4e4e4;
    --linen: #ece2cc;
    --night: #1e1e1f;
    --amber: #c8741b;
    --ink: #151515;
    --sky: #5bb8d6;
    --card-w: 1056px;
    --card-h: 600px;
  }
  * { margin: 0; padding: 0; box-sizing: border-box; }
  html, body {
    width: 1200px; height: 960px; overflow: hidden;
    background: var(--backdrop);
    font-family: "Oswald", sans-serif;
  }
  .business-card {
    position: absolute; left: 72px; top: 180px;
    width: var(--card-w); height: var(--card-h);
    background: var(--linen);
    overflow: hidden;
  }
  .card-shapes { position: absolute; inset: 0; }
  .logo-badge { position: absolute; left: 101px; top: 75px; width: 380px; height: 380px; }
  .brand-name {
    position: absolute; left: 0; width: 582px; top: 412px;
    text-align: center; color: var(--sky);
    font-size: 60px; font-weight: 500; line-height: 1;
  }
  .brand-place {
    position: absolute; left: 0; width: 582px; top: 506px;
    text-align: center; color: var(--amber);
    font-size: 22px; letter-spacing: 6px; font-weight: 500;
  }
  .contact {
    position: absolute; right: 62px; top: 62px; width: 560px;
    text-align: right; color: var(--ink);
  }
  .contact-address { font-size: 38px; line-height: 1.12; }
  .contact-phone { font-size: 50px; font-weight: 500; margin: 12px 110px 0 0; letter-spacing: 1px; }
  .offer {
    position: absolute; left: 560px; width: 400px; top: 340px; text-align: center;
  }
  .offer-title { color: var(--sky); font-size: 54px; line-height: 1.08; letter-spacing: 1px; }
  .offer-hours { color: var(--amber); font-size: 27px; font-weight: 500; margin-top: 16px; line-height: 1.5; }
  .offer-hours-days {
    display: inline-block; border-bottom: 2px solid var(--amber); line-height: 1.3;
  }
</style>
</head>
<body>
  <section class="business-card">
    <svg class="card-shapes" width="1056" height="600" viewBox="0 0 1056 600" aria-hidden="true">
      <path d="M0 232 C 200 190, 420 330, 700 300 C 860 282, 960 200, 1056 130 L1056 600 L0 600 Z" fill="var(--night)"/>
      <path d="M420 296 C 520 315, 610 308, 700 300 C 860 282, 960 200, 1056 130" fill="none" stroke="var(--amber)" stroke-width="14"/>
    </svg>

    <svg class="logo-badge" viewBox="0 0 380 380" role="img" aria-label="Round beach illustration: sunset over the ocean with a palm tree and a ship">
      <defs>
        <linearGradient id="badge-scene" x1="0" y1="0" x2="0" y2="1">
          <stop offset="0" stop-color="#f6a62a"/>
          <stop offset="0.55" stop-color="#7fc4dc"/>
          <stop offset="1" stop-color="#d49a57"/>
        </linearGradient>
      </defs>
      <circle cx="190" cy="190" r="186" fill="#9a5a22"/>
      <circle cx="190" cy="190" r="158" fill="url(#badge-scene)"/>
    </svg>

    <div class="brand-name">The Sunny Nook</div>
    <div class="brand-place">LONG BEACH, CA</div>

    <div class="contact">
      <p class="contact-address">4815C MARLOW GROVE AVENUE<br>LONG BEACH, CALIFORNIA</p>
      <p class="contact-phone">(555) 731-2294</p>
    </div>

    <div class="offer">
      <h1 class="offer-title">BREAKFAST &amp;<br>LUNCH CAFE</h1>
      <p class="offer-hours"><span class="offer-hours-days">OPEN 7 DAYS A WEEK FROM</span><br>7AM TO 2PM.</p>
    </div>
  </section>
</body>
</html>
```